Packaging design for a reclosable bag for our product

We have a logo, and we need to put it on packaging for our product and while we want the look to be simple, we want it to follow good design principles and also contain spaces for other product descriptions.

There will be 5 sizes at launch so I'd like 5 variations, one for each size.

I've included a few mockups of the type of bag that I made but they are all just rough ideas that I had.

I want the brand to look scientific and methodical and even a bit quirky, as in "wow this is a serious product but also a bit unusual."

```html
<!DOCTYPE html>
<html lang="en">
<head>
<meta charset="utf-8">
<title>QV7 Bias Lighting – 5m Pouch Front</title>
<link rel="stylesheet" href="https://fonts.googleapis.com/css2?family=Open+Sans:wght@300;400;600;700&display=swap">
<style>
  :root {
    --backdrop: #c9c9c9;
    --pouch: #0b0b0b;
    --pouch-edge: #161616;
    --ink: #ffffff;
    --ink-soft: #e6e6e6;
    --seam: #1f1f1f;
    --glow: rgba(255, 255, 255, 0.55);
  }
  * { margin: 0; padding: 0; box-sizing: border-box; }
  html, body {
    width: 1200px;
    height: 1200px;
    overflow: hidden;
    background: var(--backdrop);
    font-family: "Open Sans", Arial, sans-serif;
  }
  .canvas {
    position: relative;
    width: 1200px;
    height: 1200px;
  }
  .pouch-face {
    position: absolute;
    left: 258px;
    top: 180px;
    width: 684px;
    height: 840px;
    background: linear-gradient(100deg, var(--pouch) 0%, var(--pouch-edge) 50%, var(--pouch) 100%);
    border-radius: 4px;
    overflow: hidden;
  }
  .zip-seal {
    position: absolute;
    left: 34px;
    right: 34px;
    top: 76px;
    height: 3px;
    background: var(--seam);
  }
  .brand-glow {
    position: absolute;
    left: 40px;
    top: 120px;
    width: 604px;
    height: 400px;
    background: radial-gradient(ellipse 48% 44% at 50% 50%, var(--glow) 0%, rgba(255,255,255,0.18) 45%, rgba(255,255,255,0) 72%);
  }
  .brand-name {
    position: absolute;
    left: 124px;
    top: 220px;
    width: 415px;
    height: 220px;
    display: flex;
    align-items: center;
    justify-content: center;
    color: var(--ink);
    font-weight: 700;
    font-size: 190px;
    letter-spacing: -4px;
    line-height: 1;
  }
  .product-title {
    position: absolute;
    left: 52px;
    top: 580px;
    width: 404px;
    color: var(--ink);
    font-weight: 300;
    font-size: 48px;
    letter-spacing: 1px;
    line-height: 1;
    padding-bottom: 10px;
    border-bottom: 2px solid var(--ink);
  }
  .product-subtitle {
    position: absolute;
    left: 52px;
    top: 652px;
    color: var(--ink-soft);
    font-weight: 400;
    font-size: 23px;
    letter-spacing: 0.3px;
  }
  .feature-row {
    position: absolute;
    left: 68px;
    top: 718px;
    display: flex;
    gap: 10px;
  }
  .feature-badge {
    height: 52px;
    border: 2px solid var(--ink);
    border-radius: 6px;
    display: flex;
    flex-direction: column;
    align-items: center;
    justify-content: center;
    color: var(--ink);
    font-size: 11px;
    font-weight: 600;
    line-height: 1.1;
    padding: 2px 6px;
  }
  .feature-badge svg { display: block; margin-bottom: 2px; }
  .feature-badge.daylight { width: 64px; }
  .feature-badge.wireless { width: 98px; }
  .feature-badge.rendering { width: 64px; }
  .size-mark {
    position: absolute;
    left: 528px;
    top: 736px;
    color: var(--ink);
    text-align: left;
  }
  .size-mark .length {
    display: block;
    font-weight: 600;
    font-size: 40px;
    line-height: 1;
    letter-spacing: -1px;
    border-bottom: 2px solid var(--ink);
    width: 62px;
  }
  .size-mark .size-label {
    display: block;
    font-weight: 700;
    font-size: 8px;
    letter-spacing: 0.4px;
    margin-top: 2px;
  }
</style>
</head>
<body>
  <main class="canvas">
    <section class="pouch-face" aria-label="5m bias lighting pouch front">
      <div class="zip-seal"></div>
      <div class="brand-glow"></div>
      <div class="brand-name">QV7</div>

      <h1 class="product-title">BIAS LIGHTING</h1>
      <p class="product-subtitle">6500K White Bias Lighting</p>

      <div class="feature-row">
        <div class="feature-badge daylight">
          <svg width="26" height="26" viewBox="0 0 26 26" aria-hidden="true">
            <g stroke="#fff" stroke-width="1.6" stroke-linecap="round">
              <line x1="13" y1="1" x2="13" y2="4"/><line x1="13" y1="22" x2="13" y2="25"/>
              <line x1="1" y1="13" x2="4" y2="13"/><line x1="22" y1="13" x2="25" y2="13"/>
              <line x1="4.5" y1="4.5" x2="6.6" y2="6.6"/><line x1="19.4" y1="19.4" x2="21.5" y2="21.5"/>
              <line x1="4.5" y1="21.5" x2="6.6" y2="19.4"/><line x1="19.4" y1="6.6" x2="21.5" y2="4.5"/>
            </g>
            <circle cx="13" cy="13" r="6.5" fill="none" stroke="#fff" stroke-width="1.6"/>
            <text x="13" y="15.5" font-size="6.5" font-weight="700" fill="#fff" text-anchor="middle" font-family="Open Sans, sans-serif">D65</text>
          </svg>
          Simulated
        </div>
        <div class="feature-badge wireless">
          <svg width="22" height="26" viewBox="0 0 22 26" aria-hidden="true">
            <path d="M5 6 Q11 1 17 6" fill="none" stroke="#fff" stroke-width="1.5" stroke-linecap="round"/>
            <path d="M7.5 9 Q11 6 14.5 9" fill="none" stroke="#fff" stroke-width="1.5" stroke-linecap="round"/>
            <rect x="7" y="11" width="8" height="14" rx="1.5" fill="none" stroke="#fff" stroke-width="1.5"/>
            <circle cx="11" cy="15" r="1.3" fill="#fff"/>
          </svg>
          Wireless Control
        </div>
        <div class="feature-badge rendering">
          <svg width="26" height="26" viewBox="0 0 26 26" aria-hidden="true">
            <circle cx="13" cy="13" r="11" fill="none" stroke="#fff" stroke-width="3" stroke-dasharray="3 2"/>
            <circle cx="13" cy="13" r="7.5" fill="#fff"/>
            <text x="13" y="15.3" font-size="6" font-weight="700" fill="#0b0b0b" text-anchor="middle" font-family="Open Sans, sans-serif">CRI</text>
          </svg>
          90+
        </div>
      </div>

      <div class="size-mark">
        <span class="length">5m</span>
        <span class="size-label">EXTRA LARGE</span>
      </div>
    </section>
  </main>
</body>
</html>
```